SaaS Early tech startup business card design

Unique design for experience ecommerce platform company. the business cards will be used by executive members. conformance with color code is required.

```html
<!DOCTYPE html>
<html lang="en">
<head>
<meta charset="utf-8">
<title>Velto business card</title>
<link href="https://fonts.googleapis.com/css2?family=Roboto:wght@400;500;700;900&display=swap" rel="stylesheet">
<style>
  :root {
    --ink-blue: #0b5a8c;
    --deep-blue: #0d4f82;
    --teal: #1fb394;
    --sea: #17889f;
    --mint: #48c2a5;
    --text-grey: #4a4f55;
    --paper: #ffffff;
    --backdrop: #d9dadb;
  }
  * { box-sizing: border-box; margin: 0; padding: 0; }
  html, body { width: 1200px; height: 800px; overflow: hidden; }
  body {
    background: var(--backdrop);
    font-family: "Roboto", Arial, sans-serif;
    position: relative;
  }
  .card {
    position: absolute;
    left: 300px;
    width: 600px;
    height: 343px;
    box-shadow: 0 6px 18px rgba(0,0,0,0.18);
  }
  .card--front { top: 40px; }
  .card--back { top: 417px; }

  .mosaic {
    position: absolute;
    inset: 0;
    background:
      linear-gradient(135deg, rgba(13,79,130,0.55), rgba(31,179,148,0.35) 50%, rgba(23,136,159,0.55)),
      linear-gradient(45deg, var(--sea), var(--teal) 45%, var(--deep-blue));
  }
  .card__panel {
    position: absolute;
    background: var(--paper);
  }
  .card--front .card__panel { inset: 24px; }
  .card--back .card__panel {
    top: 78px; bottom: 78px; left: 70px; right: 70px;
    border: 2px solid var(--deep-blue);
    display: flex; align-items: center; justify-content: center;
  }

  .identity {
    position: absolute;
    right: 272px;
    top: 128px;
    text-align: right;
  }
  .identity__name {
    font-weight: 900;
    font-size: 26px;
    letter-spacing: 0.5px;
    color: var(--ink-blue);
    line-height: 1;
  }
  .identity__role {
    font-weight: 500;
    font-size: 15px;
    color: var(--teal);
    margin-top: 2px;
  }
  .divider {
    position: absolute;
    left: 290px;
    top: 70px;
    width: 1px;
    height: 160px;
    background: linear-gradient(var(--paper), var(--ink-blue) 40%, var(--paper));
  }
  .contacts {
    position: absolute;
    left: 312px;
    top: 62px;
    list-style: none;
    font-size: 13.5px;
    color: var(--text-grey);
    line-height: 17px;
  }
  .contacts li {
    display: flex;
    align-items: flex-start;
    gap: 8px;
  }
  .contacts li + li { margin-top: 1px; }
  .contacts .address { margin-bottom: 6px; }
  .contacts svg {
    flex: none;
    width: 12px;
    height: 12px;
    margin-top: 3px;
    fill: var(--teal);
  }

  .brand {
    display: flex;
    align-items: center;
    gap: 16px;
  }
  .brand__mark {
    width: 30px; height: 30px;
    background: var(--teal);
  }
  .brand__name {
    font-weight: 900;
    font-size: 92px;
    color: var(--ink-blue);
    line-height: 1;
    letter-spacing: -1px;
  }
</style>
</head>
<body>

<section class="card card--front">
  <div class="mosaic" role="img" aria-label="Border of blue and teal mosaic squares"></div>
  <div class="card__panel">
    <div class="identity">
      <p class="identity__name">DANIEL HART</p>
      <p class="identity__role">President</p>
    </div>
    <div class="divider"></div>
    <ul class="contacts">
      <li class="address">
        <svg viewBox="0 0 12 12"><path d="M6 0a4 4 0 0 0-4 4c0 3 4 8 4 8s4-5 4-8a4 4 0 0 0-4-4zm0 5.5A1.5 1.5 0 1 1 6 2.5a1.5 1.5 0 0 1 0 3z"/></svg>
        <span>412 Birchwood Road<br>Fairbanks, Alaska 99701</span>
      </li>
      <li>
        <svg viewBox="0 0 12 12"><path d="M2.5 0.5l2 2.5-1.2 1.4c.8 1.6 2 2.8 3.6 3.6L8.3 6.8l2.7 2-1 2.4C5 11 1 7 .5 1.7z"/></svg>
        <span>555-014-2231</span>
      </li>
      <li>
        <svg viewBox="0 0 12 12"><path d="M2 1h8v10H2zm1.3 1.3v6.4h5.4V2.3z"/></svg>
        <span>555-018-7740</span>
      </li>
      <li>
        <svg viewBox="0 0 12 12"><path d="M3 1h5v3H3zM1 5h10v6H1zm2 2v1h2V7z"/></svg>
        <span>555-016-3092</span>
      </li>
      <li>
        <svg viewBox="0 0 12 12"><path d="M0 2h12v8H0zm1.2 1.2L6 6.6l4.8-3.4z"/></svg>
        <span>hello@velto.com</span>
      </li>
      <li>
        <svg viewBox="0 0 12 12"><path d="M6 0a6 6 0 1 0 0 12A6 6 0 0 0 6 0zm0 1.3c.8.9 1.3 2.5 1.4 4H4.6c.1-1.5.6-3.1 1.4-4zM4.6 6.7h2.8c-.1 1.5-.6 3.1-1.4 4-.8-.9-1.3-2.5-1.4-4z"/></svg>
        <span>www.velto.com</span>
      </li>
    </ul>
  </div>
</section>

<section class="card card--back">
  <div class="mosaic" role="img" aria-label="Full background of blue and teal mosaic squares"></div>
  <div class="card__panel">
    <div class="brand">
      <span class="brand__mark"></span>
      <span class="brand__name">velto</span>
    </div>
  </div>
</section>

</body>
</html>
```